Weight Loss water drink label for "Summit Lean Glow" drinks

We need a label design for our new exciting water based weight loss drink called " Summit Lean Glow " weight loss water. It is a carb blocking, calorie burning health drink that assists in weight loss amongst men and woman. The drink is 100% natural with no sugar added. The drink comes in flavours like refreshing lemon, tropical berry and smooth strawberry. The label is for a 500ml bottle and needs to incorporate text on the label. I have uploaded a previous design to the task but feel free to be creative if you have a better idea. the label needs to stand out in the crowd and also be simple and use colour. The label has to appeal to the general public.

Target Market(s)

Our target market is men and woman between the ages of 18 and 65 that are either interested in losing weight or a living healthy

Industry/Entity Type

Health And Wellness

Font styles to use
Script

Requirements
Must have
• Must have the title " Summit Lean Glow " weight loss drink on the label as the title
• Must be a complete label design for a 500ml water bottle.
• Must have colour
• Must be unique
Nice to have
• The shape of a man and a woman's in shape physique as part of the label, not the same shapes used in the uploaded design, must look more details.
Should not have
• No colour or creativity

```html
<!DOCTYPE html>
<html lang="en">
<head>
<meta charset="utf-8">
<title>Summit Lean Glow – Weight Loss Drink Labels</title>
<link rel="stylesheet" href="https://fonts.googleapis.com/css2?family=Oswald:wght@400&display=swap">
<style>
  :root {
    --paper: #ffffff;
    --blue-light: #6fc3f2;
    --blue: #1e8fd8;
    --blue-deep: #0a63b4;
    --blue-ink: #1a86d6;
    --orange: #f7a81b;
    --silver-light: #f2f2f2;
    --silver: #c9c9c9;
    --silver-dark: #8e8e8e;
    --cap-light: #8a8a8a;
    --cap-dark: #3e3e3e;
    --white: #ffffff;
  }
  html, body {
    margin: 0;
    padding: 0;
    width: 1154px;
    height: 1200px;
    overflow: hidden;
    background: var(--paper);
  }
  .label-sheet {
    display: block;
    width: 1154px;
    height: 1200px;
  }
  .product-name,
  .tagline {
    font-family: "Oswald", "Arial Narrow", sans-serif;
    font-weight: 400;
  }
  .product-name {
    font-size: 84px;
    letter-spacing: 2px;
  }
  .product-name--orange { fill: var(--orange); }
  .product-name--blue { fill: var(--blue-ink); }
  .tagline {
    font-size: 40px;
    text-anchor: middle;
  }
  .tagline--white { fill: var(--white); }
  .tagline--blue { fill: var(--blue-ink); }
</style>
</head>
<body>
<svg class="label-sheet" viewBox="0 0 1000 1040" xmlns="http://www.w3.org/2000/svg">
  <defs>
    <linearGradient id="cap-metal" x1="0" x2="1" y1="0" y2="0">
      <stop offset="0" stop-color="var(--cap-dark)"/>
      <stop offset="0.45" stop-color="var(--cap-light)"/>
      <stop offset="1" stop-color="var(--cap-dark)"/>
    </linearGradient>
    <linearGradient id="band-metal" x1="0" x2="1">
      <stop offset="0" stop-color="var(--silver-dark)"/>
      <stop offset="0.4" stop-color="var(--silver-light)"/>
      <stop offset="1" stop-color="var(--silver-dark)"/>
    </linearGradient>
    <radialGradient id="blue-body" cx="0.35" cy="0.25" r="0.8">
      <stop offset="0" stop-color="var(--blue-light)"/>
      <stop offset="0.5" stop-color="var(--blue)"/>
      <stop offset="1" stop-color="var(--blue-deep)"/>
    </radialGradient>
    <linearGradient id="silver-body" x1="0" x2="1">
      <stop offset="0" stop-color="var(--silver)"/>
      <stop offset="0.35" stop-color="var(--silver-light)"/>
      <stop offset="1" stop-color="var(--silver-dark)"/>
    </linearGradient>
    <linearGradient id="figures-blue" x1="0" x2="0" y1="0" y2="1">
      <stop offset="0" stop-color="#0d5fa8" stop-opacity="0.55"/>
      <stop offset="1" stop-color="#0d5fa8" stop-opacity="0.2"/>
    </linearGradient>
    <linearGradient id="figures-grey" x1="0" x2="0" y1="0" y2="1">
      <stop offset="0" stop-color="#777" stop-opacity="0.55"/>
      <stop offset="1" stop-color="#777" stop-opacity="0.2"/>
    </linearGradient>
  </defs>

  <g class="bottle bottle--blue">
    <path class="bottle-cap" d="M250 150 L250 70 Q250 20 320 20 Q392 20 392 70 L392 150 Z" fill="url(#cap-metal)"/>
    <ellipse class="cap-loop" cx="321" cy="82" rx="42" ry="44" fill="var(--paper)"/>
    <rect class="cap-collar" x="205" y="150" width="235" height="25" fill="url(#band-metal)"/>
    <path class="bottle-body" d="M205 175 H440 V220 Q440 290 482 310 V998 H163 V310 Q205 290 205 220 Z" fill="url(#blue-body)"/>
    <rect class="neck-band" x="205" y="175" width="235" height="14" fill="var(--blue-deep)"/>
    <rect class="shoulder-band" x="163" y="318" width="319" height="16" fill="url(#band-metal)"/>
    <rect class="base-band" x="163" y="990" width="319" height="12" fill="url(#band-metal)"/>
    <rect class="figures" x="195" y="340" width="240" height="540" rx="60" fill="url(#figures-blue)" role="img" aria-label="Silhouettes of an athletic man and woman"/>
    <text class="product-name product-name--orange" transform="translate(352 890) rotate(-90)" textLength="540" lengthAdjust="spacingAndGlyphs">SUMMIT LEAN GLOW</text>
    <text class="tagline tagline--white" x="322" y="968">Weight Loss Drink</text>
  </g>

  <g class="bottle bottle--silver">
    <path class="bottle-cap" d="M625 150 L625 70 Q625 20 695 20 Q767 20 767 70 L767 150 Z" fill="url(#cap-metal)"/>
    <ellipse class="cap-loop" cx="696" cy="82" rx="42" ry="44" fill="var(--paper)"/>
    <rect class="cap-collar" x="580" y="150" width="235" height="25" fill="url(#band-metal)"/>
    <path class="bottle-body" d="M580 175 H815 V220 Q815 290 857 310 V998 H538 V310 Q580 290 580 220 Z" fill="url(#silver-body)"/>
    <rect class="neck-band" x="580" y="175" width="235" height="14" fill="var(--silver-dark)"/>
    <rect class="shoulder-band" x="538" y="318" width="319" height="16" fill="url(#band-metal)"/>
    <rect class="base-band" x="538" y="990" width="319" height="12" fill="url(#band-metal)"/>
    <rect class="figures" x="570" y="340" width="240" height="540" rx="60" fill="url(#figures-grey)" role="img" aria-label="Silhouettes of an athletic man and woman"/>
    <text class="product-name product-name--blue" transform="translate(727 890) rotate(-90)" textLength="540" lengthAdjust="spacingAndGlyphs">SUMMIT LEAN GLOW</text>
    <text class="tagline tagline--blue" x="697" y="968">Weight Loss Drink</text>
  </g>
</svg>
</body>
</html>
```